I need a flyer made , the flyer can be one page or two pages or three pages . I will be posting this on Instagram and social media platforms. I am a luxury home builder , I am looking to hire a construction project manager . Below are some examples and ideas what can be on the flyer

We’re looking for a construction project manager who’s passionate about building luxury homes at the highest standards
We’re hiring construction project manager
* Experience 5+ years in residential project management with a strong portfolio of completed homes.
* location : Bergen County NJ
* excellent leadership skills, leads teams with confidence and clarity
* communicates seamlessly with architects , engineers, designers and clients
*knows how to manage budgets and timelines without compromising quality
*solves problems with a positive solution first mindset
* pays attention to every detail because in luxury the small things are the big things

Apply now , link in bio or DM to connect.

My logo is attached, my web site www.velstridebuilders.com
My style is modern but still warm and inviting. I like a clean classy look .

Please don’t add any images of chairs or people to the flyer , I do not want people on my flyer. Do not add standard images of offices and houses , we are luxury builders , we build homes over 2 million dollars. Keep a classy , simple modern look . High end .

You can add a white hard hat with my logo on it for a image , this is a suggestion does not have to be on my flyer ,

```html
<!DOCTYPE html>
<html lang="en">
<head>
<meta charset="utf-8">
<title>Velstride Builders – We're Hiring</title>
<link rel="stylesheet" href="https://fonts.googleapis.com/css2?family=Poppins:wght@300;400;500;700;800&display=swap">
<style>
  :root {
    --stage: #cdd2d9;
    --paper: #eff1f0;
    --ink: #111111;
    --white: #ffffff;
    --muted: #5f6468;
    --band: #000000;
    --shadow: rgba(40, 50, 60, 0.28);
  }
  * { box-sizing: border-box; margin: 0; padding: 0; }
  html, body {
    width: 1200px; height: 655px; overflow: hidden;
    background: var(--stage);
    font-family: "Poppins", sans-serif;
  }
  .board { position: relative; width: 1200px; height: 655px; }

  .flyer {
    position: absolute; top: 85px; width: 489px; height: 489px;
    background: var(--paper); overflow: hidden;
    box-shadow: 0 6px 14px var(--shadow);
  }
  .flyer--cover { left: 95px; }
  .flyer--details { left: 596px; }

  /* Cover */
  .cover-photo {
    position: absolute; left: 0; top: 0; width: 489px; height: 448px;
    background: linear-gradient(180deg,
      #1f2740 0%, #3a3f5e 18%, #8a6c86 30%, #d7a08a 38%,
      #c9b8a8 46%, #8c8a86 60%, #4a4a44 72%, #2f4a22 82%, #1e3a18 100%);
  }
  .logo-plate {
    position: absolute; right: 0; top: 12px; width: 169px; height: 49px;
    background: var(--band);
    display: flex; align-items: center; justify-content: center;
  }
  .logo-name {
    font-family: "Poppins", sans-serif; font-weight: 500;
    letter-spacing: 1.5px; text-transform: uppercase;
    color: var(--white); font-size: 13px; white-space: nowrap;
  }
  .headline-top {
    position: absolute; left: 0; width: 473px; top: 84px;
    text-align: center;
    color: var(--white); font-weight: 300; font-size: 68px; line-height: 1;
    letter-spacing: -1px;
  }
  .headline-main {
    position: absolute; left: 94px; top: 305px;
    font-weight: 800; font-size: 90px; line-height: 1;
    letter-spacing: -3px; white-space: nowrap;
    color: var(--white);
  }
  .cover-footer {
    position: absolute; left: 0; bottom: 0; width: 100%; height: 41px;
    display: flex; align-items: center; justify-content: center;
  }
  .site-url {
    font-weight: 300; font-size: 14px; letter-spacing: 3.4px; color: var(--muted);
  }

  /* Details */
  .details-logo {
    position: absolute; top: 24px; left: 0; width: 100%;
    text-align: center;
  }
  .details-logo .logo-name { color: var(--ink); font-size: 20px; letter-spacing: 2px; }
  .intro {
    position: absolute; left: 18px; top: 84px; width: 462px;
    font-size: 13.4px; line-height: 16px; color: var(--ink); font-weight: 400;
  }
  .role-band {
    position: absolute; left: 0; top: 132px; width: 100%; height: 23px;
    background: linear-gradient(90deg, #000 0%, #000 55%, #4a4a4a 82%, rgba(0,0,0,0) 100%);
    color: var(--white); font-size: 14.5px; font-weight: 400;
    line-height: 23px; padding-left: 18px; white-space: nowrap;
  }
  .requirements {
    position: absolute; left: 18px; top: 173px; width: 460px;
    list-style: none;
  }
  .requirements li {
    position: relative; padding-left: 9px;
    font-size: 8.6px; font-weight: 300; color: var(--ink);
    line-height: 19.6px; white-space: nowrap;
  }
  .requirements li::before {
    content: ""; position: absolute; left: 0; top: 8px;
    width: 4px; height: 4px; background: var(--ink);
  }
  .details-photo {
    position: absolute; left: 0; top: 300px; width: 100%; height: 189px;
    background: linear-gradient(180deg,
      rgba(239,241,240,0) 0%, #e8cdb8 14%, #c8a89a 24%, #7f7f86 40%,
      #4b5048 58%, #2c3327 78%, #0d0f0c 100%);
  }
  .apply-banner {
    position: absolute; left: 0; top: 351px; width: 229px; height: 36px;
  }
  .apply-banner svg { position: absolute; inset: 0; }
  .apply-text {
    position: absolute; left: 18px; top: 6px; color: var(--white); line-height: 12px;
  }
  .apply-text strong { display: block; font-weight: 700; font-size: 13px; }
  .apply-text span { display: block; font-weight: 400; font-size: 11px; white-space: nowrap; }
  .details-url {
    position: absolute; left: 0; bottom: 14px; width: 100%; text-align: center;
  }
  .details-url .site-url { color: rgba(255,255,255,0.75); }
</style>
</head>
<body>
<main class="board">

  <section class="flyer flyer--cover">
    <div class="cover-photo" role="img" aria-label="Modern luxury home at dusk with glowing windows, pool and green lawn"></div>
    <div class="logo-plate"><span class="logo-name">Velstride Builders</span></div>
    <h1 class="headline-top">WE’RE</h1>
    <p class="headline-main">HIRING</p>
    <footer class="cover-footer"><span class="site-url">www.velstridebuilders.com</span></footer>
  </section>

  <section class="flyer flyer--details">
    <div class="details-photo" role="img" aria-label="Aerial view of a luxury estate home at sunset with lit windows"></div>
    <div class="details-logo"><span class="logo-name">Velstride Builders</span></div>
    <p class="intro">We’re looking for a construction project manager who’s passionate about building luxury homes at the highest standards</p>
    <h2 class="role-band">WE’RE HIRING CONSTRUCTION PROJECT MANAGER</h2>
    <ul class="requirements">
      <li>Experience 5+ years in residential project management with a strong portfolio of completed homes</li>
      <li>Location : Bergen County NJ</li>
      <li>Excellent leadership skills, leads teams with confidence and clarity</li>
      <li>Communicates seamlessly with architects, engineers, designers and clients</li>
      <li>Knows how to manage budgets and timelines without compromising quality</li>
      <li>Solves problems with a positive solution first mindset</li>
      <li>Pays attention to every detail because in luxury the small things are the big things</li>
    </ul>
    <div class="apply-banner">
      <svg width="229" height="36" viewBox="0 0 229 36"><polygon points="0,0 208,0 229,36 0,36" fill="#000"/></svg>
      <p class="apply-text"><strong>APPLY NOW,</strong><span>LINK IN BIO OR DM TO CONNECT</span></p>
    </div>
    <footer class="details-url"><span class="site-url">www.velstridebuilders.com</span></footer>
  </section>

</main>
</body>
</html>
```